Business Card Design & Gift cards, Gift Cert, Donation Card

Retail Gift Store-in addition to Business Cards we'd like sequenced 2 sided Gift cards, Gift Certificate Cards, and Donation Cards.please see examples and email for clarificationlogos attached with examples-
Gift Card, Gift Certificate and Donation Card will all be same style just differant upper right title, with back side info as example.
business card, as example is single sided.
looking for additional ideas for layout

Industry/Entity Type

Business

Contact Information for Business Card

211 Newman St.East Tawas, MI 48730989.362.8730Office@BrewKrew.com

Requirements
Must have
• Blue as per example
• Logos provided
• like gradiant background

```html
<!DOCTYPE html>
<html lang="en">
<head>
<meta charset="utf-8">
<title>Tillow Marsh — Business Card</title>
<link rel="stylesheet" href="https://fonts.googleapis.com/css2?family=Open+Sans:wght@400;600&display=swap">
<style>
  :root {
    --page: #e9ecef;
    --sky-top: #86bbe0;
    --sky-bottom: #e6eef5;
    --ink: #1c1c1c;
    --royal: #2f46a3;
    --sun: #ece000;
    --white: #ffffff;
  }
  * { margin: 0; padding: 0; box-sizing: border-box; }
  html, body {
    width: 1200px; height: 902px; overflow: hidden;
    background: var(--page);
    font-family: "Open Sans", Arial, sans-serif;
  }
  .card {
    position: absolute; left: 40px; top: 131px;
    width: 1120px; height: 640px;
    background: linear-gradient(180deg, var(--sky-top) 0%, var(--sky-bottom) 72%);
    box-shadow: 0 6px 24px rgba(0,0,0,0.18);
    overflow: hidden;
  }
  .card__waves { position: absolute; inset: 0; width: 100%; height: 100%; }
  .brand-art {
    position: absolute; left: 110px; top: 150px;
    width: 360px; height: 360px;
    border-radius: 18px;
    background: linear-gradient(160deg, rgba(47,70,163,0.55) 0%, rgba(47,70,163,0.35) 55%, rgba(236,224,0,0.6) 100%);
  }
  .brand-name {
    position: absolute; right: 80px; top: 36px;
    font-size: 64px; font-weight: 400; color: var(--ink);
    letter-spacing: 1px; line-height: 1.2;
  }
  .contact {
    position: absolute; right: 40px; top: 150px;
    list-style: none; text-align: right;
  }
  .contact__item {
    display: flex; align-items: center; justify-content: flex-end;
    gap: 16px; height: 40px;
    font-size: 23px; color: var(--ink);
  }
  .contact__icon {
    width: 26px; height: 26px; background: var(--royal);
    border-radius: 3px; display: flex; align-items: center; justify-content: center;
    flex: none;
  }
  .contact__icon svg { width: 16px; height: 16px; }
</style>
</head>
<body>
  <main class="card">
    <svg class="card__waves" viewBox="0 0 1120 640" preserveAspectRatio="none" aria-hidden="true">
      <path d="M0,600 C400,575 750,510 900,430 C1000,375 1060,352 1120,348 L1120,640 L0,640 Z" fill="var(--sun)"/>
      <path d="M0,586 C400,560 750,495 895,415 C995,360 1058,338 1120,334" fill="none" stroke="var(--white)" stroke-width="12"/>
      <path d="M0,570 C400,544 745,478 890,398 C990,343 1055,322 1120,318" fill="none" stroke="var(--royal)" stroke-width="11"/>
    </svg>

    <div class="brand-art" role="img" aria-label="Brand illustration: dancing figure stepping over a rising sun"></div>

    <h1 class="brand-name">Tillow Marsh</h1>

    <ul class="contact">
      <li class="contact__item">989.517.4296
        <span class="contact__icon"><svg viewBox="0 0 16 16"><path d="M4 2 L6 2 L7 5 L5.5 6.5 Q7 9.5 9.5 10.5 L11 9 L14 10 L14 12 Q13 14 11 14 Q3 12 2 4 Q2 2 4 2 Z" fill="#fff"/></svg></span>
      </li>
      <li class="contact__item">Office@TillowMarsh.com
        <span class="contact__icon"><svg viewBox="0 0 16 16"><rect x="2" y="4" width="12" height="8" fill="none" stroke="#fff" stroke-width="1.4"/><path d="M2 4 L8 9 L14 4" fill="none" stroke="#fff" stroke-width="1.4"/></svg></span>
      </li>
      <li class="contact__item">482 Larkfield Ave. Pine Harbor, MI 48712
        <span class="contact__icon"><svg viewBox="0 0 16 16"><path d="M8 15 C4 10 3.5 8 3.5 6.5 A4.5 4.5 0 0 1 12.5 6.5 C12.5 8 12 10 8 15 Z" fill="#fff"/><circle cx="8" cy="6.5" r="1.6" fill="var(--royal)"/></svg></span>
      </li>
    </ul>
  </main>
</body>
</html>
```